Hi everyone,
Fresh Walls Co is a business that renovates older houses into modern homes. I'm looking for a design that is clean and simple. It needs to show the client that renovating is a simple process. No more than 3 colours to be used thanks.

What I need:
1. Logo
2. Business card (one side)
3. Letter head (A4)

Looking forward to the designs!

Construction

Fresh Walls Co

Sans Serif

Must have
• Trading name: Fresh Walls Co
• Contact name: Declan Ashworth
• Email: declanashworth@freshwallsco.example.com.au
• Tel: 0412 758 204
• Clean and simple
Nice to have
• If design might include a few tools. eg Hammer, paint roller etc.
Should not have
• Complicated design

```html
<!DOCTYPE html>
<html lang="en">
<head>
<meta charset="utf-8">
<title>Fresh Walls Co – Business Card</title>
<link rel="stylesheet" href="https://fonts.googleapis.com/css2?family=Roboto+Condensed:wght@400;700&display=swap">
<style>
  :root {
    --brand-red: #e31e25;
    --charcoal: #3b3b3d;
    --paper: #ffffff;
    --backdrop: #e9e7e4;
  }
  html, body {
    margin: 0;
    padding: 0;
    width: 1200px;
    height: 800px;
    overflow: hidden;
    background: var(--backdrop);
    font-family: "Roboto Condensed", "Arial Narrow", sans-serif;
  }
  .business-card {
    position: absolute;
    left: 100px;
    top: 95px;
    width: 1000px;
    height: 611px;
    background: var(--paper);
    overflow: hidden;
    box-shadow: 0 6px 24px rgba(0,0,0,0.12);
  }
  .card-shapes {
    position: absolute;
    inset: 0;
    width: 1000px;
    height: 611px;
  }
  .red-field { fill: var(--brand-red); }
  .swoosh { fill: none; stroke: var(--charcoal); stroke-width: 14; stroke-linecap: round; }

  .wordmark {
    position: absolute;
    left: 70px;
    top: 215px;
    display: flex;
    align-items: center;
    gap: 16px;
    color: var(--brand-red);
    font-weight: 700;
    font-size: 60px;
    line-height: 1;
    letter-spacing: 0.5px;
    white-space: nowrap;
  }
  .wordmark-square {
    width: 26px;
    height: 26px;
    background: var(--brand-red);
  }

  .contact {
    position: absolute;
    color: var(--paper);
    right: 110px;
    text-align: right;
    white-space: nowrap;
    line-height: 1;
  }
  .contact-name {
    top: 345px;
    right: 50px;
    font-weight: 700;
    font-size: 42px;
    letter-spacing: 1px;
    text-transform: uppercase;
  }
  .contact-email {
    top: 425px;
    font-size: 23px;
  }
  .contact-phone {
    top: 480px;
    font-size: 28px;
  }
  .contact-icon {
    position: absolute;
    right: 55px;
    width: 36px;
    height: 36px;
  }
  .icon-mail { top: 419px; }
  .icon-phone { top: 476px; }
</style>
</head>
<body>
  <div class="business-card">
    <svg class="card-shapes" viewBox="0 0 1000 611" aria-hidden="true">
      <path class="red-field" d="M 330 611 C 420 400, 650 210, 1000 130 L 1000 611 Z"/>
      <path class="swoosh" d="M 400 420 C 500 290, 700 150, 1010 80"/>
    </svg>

    <div class="wordmark">
      <span class="wordmark-square"></span>
      <span class="wordmark-name">Fresh Walls Co</span>
    </div>

    <div class="contact contact-name">Declan Ashworth</div>
    <div class="contact contact-email">declanashworth@freshwallsco.example.com.au</div>
    <div class="contact contact-phone">0412 758 204</div>

    <svg class="contact-icon icon-mail" viewBox="0 0 40 40" aria-label="Email">
      <rect x="3" y="9" width="34" height="22" fill="#ffffff"/>
      <path d="M 3 9 L 20 23 L 37 9" fill="none" stroke="#e31e25" stroke-width="2.5"/>
    </svg>
    <svg class="contact-icon icon-phone" viewBox="0 0 40 40" aria-label="Phone">
      <path d="M 12 6 L 18 13 L 14 17 C 16 23, 19 26, 24 28 L 28 24 L 34 30 L 29 35 C 18 33, 8 22, 7 11 Z" fill="#ffffff"/>
    </svg>
  </div>
</body>
</html>
```